Residential Mortgage Leader needs Wordpress Design

Looking for a home page website design for a client. We develop using the WordPress platform and would prefer the design be at least loosely based on an existing WordPress template. Attached files have many notes from our creative brief with client. The site must be responsive. Approved, basic wireframe attached. There is room for interpretation.

Existing web site: http://www.marisolkettering.example/

The Marisol Kettering Team relies on strong systems to deliver an on-time, done-right, friendly experience. Marisol offers mortgages and refinancing services throughout the United States. She is a successful Brookvale Funding agent who strives to be an active part of her community. She would like to focus the site on her team, rather than just her.

Difference makers...
When you work with the Marisol Kettering team you get a high level of expertise and a friendly experience.

She has amazing credentials. Marisol is widely recognized as a top producer for her company, and has earned a number of awards and honors for her customer service.

Marisol's team is very engaged and enjoys sharing social comments or photos from their community.

Imagery:
* Friendly, warm imagery, preferably of her team or an image to represent her team
* Clean and crisp
* Professional / Experts in mortgage and refinance
* Clean / Good use of white space
Updates

When possible, please use imagery from the DFW area. The client mentioned they would prefer not to see stock images. Thanks.

Amend that- creative use of stock images, however, is fine. A few designs have used stock imagery, but in a well-considered manner.

We added some photos and graphics that are local. We are Dallas / Ft. Worth, Plano, Frisco, Texas. We also added some examples of photos to use for the "In the Community" area. Stock photos of business folks just doesn't fit there. Thanks!

Target Market(s)

They service a lot of builders, but also work with homeowners. Their typical client is usually a woman searching for mortgage services online. She typically has a family and may refer her husband to Marisol's team. Keep in mind, however, they also see a number of other scenarios. Most of their clients are middle to high-end borrowers.

Industry/Entity Type

It Company

Requirements
Must have
• Design should be developed using program such as Photoshop or Fireworks or Illustrator as last preference. Ideally, the design would be based on an existing responsive WordPress theme, which we would customize. You must include the name of the target theme. The footer should include lots of space for disclaimers and legal language. Site navigation should include these choices: "Home, About, Builders, Mortgage Info, Approval, Blog, Contact"
Nice to have
• Blog, social media and photos area. Use of the already approved style prototype with colors and fonts (Lato- a Google font, Times New Roman and Cookie-a decorative Google font). However, we are open to interpretation.
Should not have
• Hard to read fonts or a lack of white space.

```html
<!DOCTYPE html>
<html lang="en">
<head>
<meta charset="utf-8">
<title>Brookvale Funding – Marisol Kettering Team</title>
<link rel="stylesheet" href="https://fonts.googleapis.com/css2?family=Source+Sans+3:wght@400;600;700&family=Open+Sans:wght@700;800&family=Cookie&display=swap">
<style>
:root{
  --red:#c8301f;
  --red-dark:#b0281a;
  --ink:#222;
  --muted:#555;
  --grey-line:#8a8a8a;
  --soft:#e9e9e9;
  --white:#fff;
  --client:#b4b4b4;
}
*{box-sizing:border-box;margin:0;padding:0}
html,body{width:1062px;height:1200px;overflow:hidden;background:var(--white)}
body{position:relative;font-family:"Source Sans 3",Arial,sans-serif;color:var(--ink);font-size:11px;line-height:1.2}
.abs{position:absolute}
a{color:inherit;text-decoration:none}

/* header */
.site-header{left:0;top:0;width:1062px;height:86px;background:var(--white)}
.brand{left:133px;top:34px}
.brand-name{font-size:23px;font-weight:700;color:var(--red);letter-spacing:-.3px}
.brand-name span{color:#555}
.brand-sub{font-size:11px;font-weight:700;color:#444;margin-top:-2px}
.work-tag{left:740px;top:16px;background:#555;color:#fff;font-size:9px;padding:2px 8px;height:15px}
.phone{left:823px;top:12px;color:var(--red);font-size:17px}
.email{left:741px;top:35px;font-size:12px;color:#666}
.main-nav{left:418px;top:60px;display:flex;gap:28px;font-size:15px;color:#555}
.main-nav .current{color:var(--red);border-top:2px solid var(--red);padding-top:1px;margin-top:-3px}

/* hero */
.hero{left:0;top:86px;width:1062px;height:480px;
  background:linear-gradient(180deg,rgba(255,255,255,0) 70%,#fff 100%),
  linear-gradient(90deg,#4f5a45 0%,#8c8a80 30%,#a09080 55%,#6c5548 75%,#3c3a36 100%)}
.hero-photo{left:134px;top:123px;width:412px;height:252px;border:6px solid #dcdcdc;
  background:linear-gradient(160deg,#6d7866,#a9a89c 40%,#6e8fa6 70%,#8a5a48)}
.hero-rule{left:604px;top:144px;width:292px;height:2px;background:#fff}
.hero-title{left:602px;top:150px;color:#fff;font-family:"Open Sans",sans-serif;font-weight:800;letter-spacing:-2.5px;line-height:.9}
.hero-title .l1{font-size:40px}
.hero-title .l2{font-size:62px;letter-spacing:-3.5px}
.hero-text{left:605px;top:259px;width:300px;color:#fff;font-size:13px;line-height:1.15}
.cta{left:603px;top:311px;height:36px;width:150px;background:var(--red);color:#fff;font-weight:700;font-size:19px;display:flex;align-items:center;padding-left:18px;gap:12px}
.cta-arrow{left:753px;top:311px}
.alt-link{left:782px;top:321px;color:#fff;font-weight:700;font-size:12.5px;display:flex;align-items:center;gap:5px}
.alt-link i{font-style:normal;background:#111;border-radius:50%;width:16px;height:16px;display:inline-flex;align-items:center;justify-content:center;font-size:9px}

/* panel */
.panel{left:133px;top:406px;width:797px;height:466px;background:var(--white);border:1px solid #ddd;border-top:none}
.card{top:426px;width:244px;height:93px;background:#fff;border:1px solid #ddd;border-bottom:3px solid var(--red);box-shadow:0 1px 2px rgba(0,0,0,.08)}
.card .thumb{position:absolute;left:17px;top:16px;width:55px;height:55px;border-radius:3px}
.card h3{position:absolute;left:82px;top:14px;font-weight:400;font-size:16px;color:var(--red);line-height:1}
.card h3 b{color:#1b5fa8}
.card p{position:absolute;left:82px;top:34px;width:150px;font-size:10.5px;line-height:1.05}
.section-title{left:0;width:1062px;top:553px;text-align:center;font-size:26px;color:#111}
.section-sub{left:0;width:1062px;top:583px;text-align:center;font-family:"Cookie",cursive;font-size:20px;color:var(--red)}
.col-head{top:632px;font-size:16px;color:#222}
.col-rule{top:659px;width:214px;height:4px;border-top:1px solid var(--grey-line);border-bottom:1px solid var(--grey-line)}
.blog-list{left:157px;top:680px;width:230px;list-style:none}
.blog-list li{height:33.5px;font-size:10.5px}
.blog-list b{color:var(--red);display:block}
.blog-list em{color:#999;font-size:8.5px}
.social-list{left:419px;top:681px;width:220px;list-style:none}
.social-list li{height:53.5px;display:flex;gap:11px}
.social-list .avatar{width:34px;height:32px;flex:none;background:linear-gradient(#b9a89a,#6d6058)}
.social-list p{font-size:10.5px;line-height:1.05}
.community{left:694px;top:682px;display:grid;grid-template-columns:repeat(3,69px);gap:14px 4px}
.tile{width:69px;height:69px;position:relative;border:1px solid #ddd}
.tile span{position:absolute;left:0;bottom:0;width:100%;height:16px;background:var(--red);color:#fff;font-size:9.5px;text-align:center;line-height:16px}

/* footer links */
.f-head{top:900px;font-size:14px;color:var(--red)}
.f-rule{top:927px;height:3px;background:#ddd}
.f-list{list-style:none;font-size:10.5px;color:#333}
.f-list li{height:21.3px;padding-left:8px;position:relative}
.f-list li::before{content:"";position:absolute;left:0;top:4px;border-left:3px solid #333;border-top:3px solid transparent;border-bottom:3px solid transparent}
.person{display:flex;gap:10px;height:43.5px;font-size:10.5px;line-height:1.05;color:#444}
.person .avatar{width:34px;height:32px;background:linear-gradient(#a48878,#5d4a40)}
.clients{left:726px;top:950px;display:grid;grid-template-columns:100px 100px;row-gap:20px;column-gap:3px}
.clients div{font-size:17px;font-weight:700;color:var(--client);display:flex;align-items:center;gap:5px;height:24px}
.clients i{width:12px;height:12px;border-radius:50%;background:var(--client);display:inline-block}

/* legal */
.legal{left:0;top:1113px;width:1062px;height:87px;background:var(--red);border-top:2px solid #e26a5a}
.legal .copy{position:absolute;left:108px;top:28px;color:#fff;font-size:9.5px}
.legal .team{position:absolute;left:630px;top:24px;color:#6a140c;font-size:17px;font-family:"Source Sans 3",sans-serif}
.legal .social-label{position:absolute;left:773px;top:33px;color:#fff;font-size:9px}
.legal .circles{position:absolute;left:823px;top:24px;display:flex;gap:4px}
.legal .circles span{width:25px;height:25px;border:2px solid #fff;border-radius:50%}
</style>
</head>
<body>

<header class="abs site-header">
  <div class="abs brand">
    <div class="brand-name">Brookvale <span>Funding</span></div>
    <div class="brand-sub">A Northfield Capital Company</div>
  </div>
  <div class="abs work-tag">WORK WITH US</div>
  <div class="abs phone">555- 014- 2290</div>
  <div class="abs email">Our email : info@brookvalefunding.example</div>
  <nav class="abs main-nav">
    <a>Home</a><a>About</a><a class="current">Builders</a><a>Mortgage Info</a><a>Approval</a><a>Blog</a><a>Contact</a>
  </nav>
</header>

<section class="abs hero" role="img" aria-label="Blurred background photo of a smiling family outside their new home"></section>
<div class="abs hero-photo" role="img" aria-label="Family standing in front of a house holding a sold for-sale sign"></div>
<div class="abs hero-rule"></div>
<h1 class="abs hero-title"><div class="l1">EARNING YOUR</div><div class="l2">BUSINESS</div></h1>
<p class="abs hero-text">Lorem ipsum dolor sit amet, consectetur adipiscing elit sit non dolor non auguefermentum dolor non augue pretium non egestas dolor amet</p>
<a class="abs cta">START HERE
  <svg width="16" height="16" viewBox="0 0 16 16"><circle cx="8" cy="8" r="8" fill="#fff"/><path d="M6 4.5 9.5 8 6 11.5" stroke="#c8301f" stroke-width="2" fill="none"/></svg></a>
<svg class="abs cta-arrow" width="12" height="36" viewBox="0 0 12 36"><path d="M0 0 12 18 0 36Z" fill="#c8301f"/></svg>
<a class="abs alt-link"><i>or</i>Get to know us</a>

<main class="abs panel"></main>

<article class="abs card" style="left:153px">
  <div class="thumb" style="background:radial-gradient(circle,#555 40%,#222 60%,#bbb 62%)" role="img" aria-label="Top originators award badge"></div>
  <h3>Our Credentials</h3>
  <p>Lorem ipsum dolor sit amet, elit sit dolor non auguefer mentum dolor non augue pretium</p>
</article>
<article class="abs card" style="left:409px">
  <div class="thumb" style="background:linear-gradient(#d6d6d6,#9aa7c0)" role="img" aria-label="Readers choice awards badge"></div>
  <h3>Readers<br>Choice' <b>Awards</b></h3>
  <p style="top:48px">www.harborlocalnews.example</p>
</article>
<article class="abs card" style="left:665px">
  <div class="thumb" style="background:linear-gradient(#6c7a68,#5f8aa8 60%,#8b5b4a)" role="img" aria-label="Family with a sold sign"></div>
  <h3>Recognion</h3>
  <p>Lorem ipsum dolor sit amet, elit sit dolor non auguefer mentum dolor non augue pretium</p>
</article>

<h2 class="abs section-title" style="font-weight:400">Engaged in Our Community</h2>
<div class="abs section-sub">---------- Connect with us ----------</div>

<h3 class="abs col-head" style="left:158px;font-weight:400">Our Blog</h3>
<div class="abs col-rule" style="left:158px"></div>
<h3 class="abs col-head" style="left:419px;font-weight:400">Social</h3>
<div class="abs col-rule" style="left:419px"></div>
<h3 class="abs col-head" style="left:694px;font-weight:400">In the Comunity</h3>
<div class="abs col-rule" style="left:694px"></div>

<ul class="abs blog-list">
  <li><b>Lorem ipsum Best Practice</b>elit sit dolor non sid augue pretium.. <em>11 Sept 2013</em></li>
  <li><b>Lorem ipsum Best Practice</b>elit sit dolor non sid augue pretium.. <em>11 Sept 2013</em></li>
  <li><b>Lorem ipsum Best Practice</b>elit sit dolor non sid augue pretium.. <em>11 Sept 2013</em></li>
  <li><b>Lorem ipsum Best Practice</b>elit sit dolor non sid augue pretium.. <em>11 Sept 2013</em></li>
  <li><b>Lorem ipsum Best Practice</b>elit sit dolor non sid augue pretium.. <em>11 Sept 2013</em></li>
</ul>

<ul class="abs social-list">
  <li><div class="avatar" role="img" aria-label="Team member portrait"></div><p><b>Lorem ipsum dolor sit amet non sit</b><br>elit sit dolor non sid augue pretium elit sid donor non auguefer auguefer ...</p></li>
  <li><div class="avatar" role="img" aria-label="Business handshake photo"></div><p><b>Lorem ipsum dolor sit amet non sit</b><br>elit sit dolor non sid augue pretium elit sid donor non auguefer auguefer ...</p></li>
  <li><div class="avatar" role="img" aria-label="Couple with sold sign"></div><p><b>Lorem ipsum dolor sit amet non sit</b><br>elit sit dolor non sid augue pretium elit sid donor non auguefer auguefer ...</p></li>
</ul>

<div class="abs community">
  <div class="tile" role="img" aria-label="Family with sold sign" style="background:linear-gradient(#6b7864,#5f8aa8)"><span>Lorem Ipsum..</span></div>
  <div class="tile" role="img" aria-label="Couple reviewing paperwork" style="background:linear-gradient(#e4dcd4,#9ab0c4)"><span>Lorem Ipsum..</span></div>
  <div class="tile" role="img" aria-label="Award badge" style="background:radial-gradient(circle,#555 40%,#ddd 60%)"><span>Lorem Ipsum..</span></div>
  <div class="tile" role="img" aria-label="Model house on documents" style="background:linear-gradient(#f2f2f2,#c7cfd9)"><span>Lorem Ipsum..</span></div>
  <div class="tile" role="img" aria-label="Woman in glasses smiling" style="background:linear-gradient(#ddd,#6c5c55)"><span>Lorem Ipsum..</span></div>
  <div class="tile" role="img" aria-label="Family with sold sign" style="background:linear-gradient(#5f6b58,#5f8aa8)"><span>Lorem Ipsum..</span></div>
</div>

<h4 class="abs f-head" style="left:133px;font-weight:600">Useful Links</h4>
<div class="abs f-rule" style="left:133px;width:214px"></div>
<ul class="abs f-list" style="left:133px;top:944px">
  <li>Home</li><li>About</li><li>Builders</li><li>Mortgage Info</li><li>Approval</li><li>Blog</li><li>Contact</li>
</ul>
<ul class="abs f-list" style="left:247px;top:944px">
  <li>Lorem Ipsum</li><li>Dummy Link</li><li>Lorem Ipsum Link</li><li>Dummy Text Link</li><li>Lorem Ipsum Text</li><li>Dummy Link</li><li>Donor Amet Non</li>
</ul>

<h4 class="abs f-head" style="left:389px;font-weight:600">Lorem Heading</h4>
<div class="abs f-rule" style="left:389px;width:120px"></div>
<div class="abs" style="left:389px;top:947px">
  <div class="person"><div class="avatar" role="img" aria-label="Portrait of Marisol Kettering"></div><div>Marisol Kettering,<br>Branch Manager<br><b>NMLS : 40218</b></div></div>
  <div class="person"><div class="avatar" role="img" aria-label="Portrait of Marisol Kettering"></div><div>Marisol Kettering,<br>Branch Manager<br><b>NMLS : 40218</b></div></div>
  <div class="person"><div class="avatar" role="img" aria-label="Portrait of Marisol Kettering"></div><div>Marisol Kettering,<br>Branch Manager<br><b>NMLS : 40218</b></div></div>
</div>

<h4 class="abs f-head" style="left:564px;font-weight:600">Language</h4>
<div class="abs f-rule" style="left:564px;width:120px"></div>
<ul class="abs f-list" style="left:564px;top:944px">
  <li>English Lorem Ipsum</li><li>French Dummy Link</li><li>Purtgole Lorem Ipsum</li><li>Chinies Dummy</li><li>English &nbsp;Lorem Ipsum</li><li>Much More</li>
</ul>

<h4 class="abs f-head" style="left:726px;font-weight:600">Our Clients</h4>
<div class="abs f-rule" style="left:726px;width:183px"></div>
<div class="abs clients">
  <div><i></i>Corvane</div><div>Halden</div>
  <div><i></i>Stratoria</div><div>Nimbrel</div>
  <div>Quillon</div><div><i></i>Corvane</div>
</div>

<footer class="abs legal">
  <div class="copy">All Right Reserved © Copyright 2013 - Terms and Conditions</div>
  <div class="team">Marisol Kettering</div>
  <div class="social-label">Our Social</div>
  <div class="circles"><span aria-label="Social profile"></span><span aria-label="Social profile"></span><span aria-label="Social profile"></span></div>
</footer>

</body>
</html>
```